Sophisticated, clean website reflecting my feminine, playful side to sell my abstract art,

I need a website no more than 3 pages to showcase my paintings, a little about me and some contact info. I do abstracts so looking for something a little edgy, yet feminine and current.
Updates

Hi there, These are some artists websites that I Iike: Marnelvoss.com (I like how airy it is) peterwallombry.com garethpolvens.com (I like how it scrolls) I'll need a place for a photo ( a headshot-i do not have it yet so I'll need to be able to upload that later) as well as an area for my bio. Also, it's important that I will be able to upload any new photos and descriptions easily so it should be user friendly. Lastly, I like in a sunny place so would like to have this seem upbeat and playful as that is how i like to paint. thanks-I'm trying to upload my photos now -

Target Market(s)

ppl ages 35-70 who want large scale art for their homes

Industry/Entity Type

art

Coding

Coded - Design and coding required

Number of Pages Required

3 page

Colors

Designer to choose colors to be used in the design.

Requirements
Must have
• photos of my art, a place for my bio, be easy to reach me. tasteful-nothing too "in your face" -my clients are pretty high end and organized. They like clean lines
Nice to have
• sophisticated background, muted tones in the back-similar clean font throughout-no cursive
Should not have
• too many dark areas. Too many blocks of color. Too serious.

```html
<!DOCTYPE html>
<html lang="en">
<head>
<meta charset="utf-8">
<title>Lena Marchetti — Abstract Art</title>
<link href="https://fonts.googleapis.com/css2?family=Heebo:wght@300;400;700&family=Questrial&display=swap" rel="stylesheet">
<style>
  :root {
    --ink: #111111;
    --text: #333333;
    --muted: #555555;
    --rule: #c9c9c9;
    --paper: #ffffff;
    --frame-gold: #cdc6ba;
    --frame-grey: #bdbdbd;
    --hero-a: #2f8f5a;
    --hero-b: #7cbf4a;
    --hero-c: #1f6f78;
    --art-a: #6b4b8a;
    --art-b: #d7c9b6;
    --art-c: #3b3a6b;
    --portrait: #efefef;
  }
  * { margin: 0; padding: 0; box-sizing: border-box; }
  html, body { width: 1200px; height: 2884px; overflow: hidden; background: var(--paper); }
  body { position: relative; font-family: "Questrial", sans-serif; color: var(--text); }
  .abs { position: absolute; }

  .brand-mark { background: var(--ink); }
  .site-title {
    left: 0; width: 1200px; top: 24px; text-align: center;
    font-family: "Heebo", sans-serif; font-weight: 300; font-size: 45px; color: var(--ink);
    letter-spacing: 0.5px; padding-left: 64px;
  }
  .header-rule { left: 0; top: 100px; width: 1200px; height: 2px; background: var(--rule); }

  .nav-link {
    transform: translateX(-50%); font-size: 16px; color: var(--ink); letter-spacing: 0.3px;
    text-transform: uppercase; white-space: nowrap;
  }
  .nav-active-bar { height: 2px; background: var(--ink); }
  .social-dot { width: 32px; height: 32px; border-radius: 50%; border: 3px solid var(--ink); }
  .social-handle { font-size: 17px; color: var(--ink); white-space: nowrap; }

  .arrow { width: 28px; height: 44px; }

  .hero-art {
    left: 84px; top: 171px; width: 1037px; height: 591px;
    background: linear-gradient(125deg, var(--hero-c) 0%, var(--hero-a) 35%, var(--hero-b) 65%, #c9cfc0 85%, var(--hero-c) 100%);
  }

  .portrait-frame { left: 83px; top: 916px; width: 409px; height: 402px; border: 2px solid var(--frame-grey); padding: 7px; }
  .portrait-photo { width: 100%; height: 100%; background: var(--portrait); }

  .section-title { font-family: "Heebo", sans-serif; font-weight: 300; color: var(--ink); white-space: nowrap; }
  .title-bar { height: 3px; background: var(--ink); }

  .about-title { left: 560px; top: 928px; font-size: 45px; }
  .about-copy { left: 560px; top: 1016px; width: 582px; font-size: 17px; line-height: 27.3px; color: var(--muted); }
  .about-copy p + p { margin-top: 14px; }

  .gallery-title { left: 0; width: 1166px; top: 1466px; text-align: center; font-size: 41px; }
  .gallery-frame {
    left: 158px; top: 1574px; width: 903px; height: 572px;
    border: 7px solid var(--frame-gold); padding: 10px; background: var(--paper);
  }
  .gallery-art {
    width: 100%; height: 100%;
    background: linear-gradient(115deg, var(--art-c) 0%, var(--art-a) 30%, #8c5a7a 50%, var(--art-b) 75%, var(--art-a) 100%);
  }

  .contact-title { left: 0; width: 1238px; top: 2282px; text-align: center; font-size: 41px; }
  .contact-line { left: 0; width: 1240px; text-align: center; color: var(--ink); }
  .contact-intro { top: 2377px; font-size: 19px; color: var(--muted); }
  .contact-email { top: 2442px; font-size: 20px; }
  .contact-phone { top: 2491px; font-size: 20px; }

  .footer-name { font-family: "Heebo", sans-serif; font-weight: 700; font-size: 28px; color: var(--ink); white-space: nowrap; }
  .footer-rule { left: 120px; top: 2809px; width: 992px; height: 2px; background: var(--rule); }
  .copyright { left: 0; width: 1212px; top: 2829px; text-align: center; font-size: 14px; color: var(--muted); }
</style>
</head>
<body>

<header>
  <div class="abs brand-mark" style="left:368px;top:31px;width:44px;height:43px;"></div>
  <h1 class="abs site-title">LENA MARCHETTI</h1>
  <div class="abs header-rule"></div>
  <nav>
    <span class="abs nav-link" style="left:209px;top:121px;">Home</span>
    <div class="abs nav-active-bar" style="left:187px;top:147px;width:45px;"></div>
    <span class="abs nav-link" style="left:387px;top:121px;">About Me</span>
    <span class="abs nav-link" style="left:579px;top:121px;">Gallery</span>
    <span class="abs nav-link" style="left:767px;top:121px;">Contact</span>
    <div class="abs social-dot" style="left:913px;top:116px;"></div>
    <span class="abs social-handle" style="left:951px;top:120px;">@lmarchettiart</span>
  </nav>
</header>

<section class="hero">
  <svg class="abs arrow" style="left:33px;top:428px;" viewBox="0 0 28 44"><path d="M22 4 L6 22 L22 40" fill="none" stroke="#111" stroke-width="6" stroke-linecap="round" stroke-linejoin="round"/></svg>
  <div class="abs hero-art" role="img" aria-label="Featured abstract painting in greens and teal with loose brushstrokes"></div>
  <svg class="abs arrow" style="left:1149px;top:428px;" viewBox="0 0 28 44"><path d="M6 4 L22 22 L6 40" fill="none" stroke="#111" stroke-width="6" stroke-linecap="round" stroke-linejoin="round"/></svg>
</section>

<section class="about">
  <div class="abs portrait-frame"><div class="portrait-photo" role="img" aria-label="Artist headshot"></div></div>
  <h2 class="abs section-title about-title">ABOUT ME</h2>
  <div class="abs title-bar" style="left:560px;top:990px;width:63px;"></div>
  <div class="abs about-copy">
    <p>Lorem ipsum dolor sit amet, consectetur adipiscing elit, sed do eiusmod tempor incididunt ut labore et dolore magna aliqua. Ut enim ad minim veniam, quis nostrud exercitation</p>
    <p>Duis aute irure dolor in reprehenderit in voluptate velit esse cillum dolore eu fugiat nulla pariatur. Excepteur sint occaecat cupidatat non proident, sunt in culpa qui officia deserunt mollit anim id est laborum.Sed ut perspiciatis unde pariatur. Excepteur sint occaecat cupidatat non proident, sunt in culpa qui officia deserunt mollit anim id est laborum.Sed ut persmollit anim id est laborum.Sed ut perspiciatis unde pariatur. Excepteur sin</p>
  </div>
</section>

<section class="gallery">
  <h2 class="abs section-title gallery-title">PAINTING GALLERY</h2>
  <div class="abs title-bar" style="left:559px;top:1527px;width:63px;"></div>
  <svg class="abs arrow" style="left:94px;top:1838px;" viewBox="0 0 28 44"><path d="M22 4 L6 22 L22 40" fill="none" stroke="#111" stroke-width="6" stroke-linecap="round" stroke-linejoin="round"/></svg>
  <div class="abs gallery-frame"><div class="gallery-art" role="img" aria-label="Abstract floral painting in purple, blue and cream"></div></div>
  <svg class="abs arrow" style="left:1097px;top:1838px;" viewBox="0 0 28 44"><path d="M6 4 L22 22 L6 40" fill="none" stroke="#111" stroke-width="6" stroke-linecap="round" stroke-linejoin="round"/></svg>
</section>

<section class="contact">
  <h2 class="abs section-title contact-title">CONTACT ME</h2>
  <div class="abs title-bar" style="left:578px;top:2342px;width:91px;"></div>
  <p class="abs contact-line contact-intro">Please get in touch with me on below details.</p>
  <p class="abs contact-line contact-email">Email : lenamarchetti@info.com</p>
  <p class="abs contact-line contact-phone">Phone: (555) 014 2368</p>
  <div class="abs social-dot" style="left:555px;top:2543px;"></div>
  <span class="abs social-handle" style="left:596px;top:2548px;">@lmarchettiart</span>
</section>

<footer>
  <div class="abs brand-mark" style="left:128px;top:2733px;width:42px;height:43px;"></div>
  <span class="abs footer-name" style="left:177px;top:2732px;">LENA MARCHETTI</span>
  <span class="abs nav-link" style="left:541px;top:2744px;">About Me</span>
  <span class="abs nav-link" style="left:687px;top:2744px;">Gallery</span>
  <span class="abs nav-link" style="left:829px;top:2744px;">Contact</span>
  <div class="abs social-dot" style="left:943px;top:2736px;"></div>
  <span class="abs social-handle" style="left:982px;top:2741px;">@lmarchettiart</span>
  <div class="abs footer-rule"></div>
  <p class="abs copyright">© 2022 Lena Marchetti &nbsp; All Rights Reserved</p>
</footer>

</body>
</html>
```